Business card for law firm

Need business card for new law firm. Think confident, authoritative, conservative, but not stuffy or old-fashioned.

Contact Information for Business Card

Content for card - logo (uploaded), plus the following:

Paul Whitcombe (larger font)
Managing Partner (larger font, but not as large as name)
Level 9, 7 Ferris Lane
Sydney NSW 2000
Main Tel 02 9364 2710
Direct Tel 02 8472 3159
Email paul@qvlegal.com.au
www.qvlegal.com.au

Letterhead design should include logo plus:
Level 9, 7 Ferris Lane
Sydney NSW 2000
Tel 02 8472 3159
www.qvlegal.com.au

```html
<!DOCTYPE html>
<html lang="en">
<head>
<meta charset="utf-8">
<title>Quayvale Legal — Business Card</title>
<link rel="stylesheet" href="https://fonts.googleapis.com/css2?family=Open+Sans:wght@400;700&display=swap">
<style>
  :root {
    --navy: #0b1f5c;
    --black: #050505;
    --white: #ffffff;
    --ink: #111111;
    --backdrop: #3a3c40;
    --icon-grey: #d8d8d8;
  }
  * { box-sizing: border-box; margin: 0; padding: 0; }
  html, body {
    width: 1200px; height: 1000px; overflow: hidden;
    background: var(--backdrop);
    font-family: "Open Sans", Arial, sans-serif;
  }
  .sheet {
    width: 1200px; height: 1000px;
    display: flex; flex-direction: column; align-items: center; justify-content: center;
    gap: 44px;
  }
  .card {
    position: relative;
    width: 760px; height: 434px;
    overflow: hidden;
    box-shadow: 0 10px 30px rgba(0,0,0,.35);
  }
  /* front */
  .card--front { background: var(--white); }
  .brand {
    position: absolute; left: 300px; top: 56px; width: 330px;
    display: flex; flex-direction: column; align-items: center;
    color: var(--ink);
  }
  .brand__mark { width: 44px; height: 44px; background: var(--navy); margin-bottom: 14px; }
  .brand__name { font-size: 46px; font-weight: 400; letter-spacing: 3px; line-height: 1; }
  .brand__tag { font-size: 14px; font-weight: 400; letter-spacing: 14px; margin-top: 6px; padding-left: 14px; }

  .holder {
    position: absolute; left: 0; top: 186px; width: 350px; height: 144px;
    background: var(--navy); color: var(--white);
    padding: 16px 0 0 58px;
  }
  .holder__name { font-size: 24px; font-weight: 700; text-transform: uppercase; line-height: 1.1; }
  .holder__role { font-size: 15px; font-weight: 700; text-transform: uppercase; margin-bottom: 6px; }
  .holder__address { font-size: 17px; line-height: 1.3; font-style: normal; }

  .accent {
    position: absolute; left: 358px; top: 186px; width: 84px; height: 210px;
    background: var(--navy);
  }
  .contact {
    position: absolute; left: 452px; top: 272px; width: 308px; height: 126px;
    background: var(--black); color: var(--white);
    padding: 14px 14px 0 0;
    list-style: none;
  }
  .contact__item {
    display: flex; justify-content: flex-end; align-items: center; gap: 10px;
    font-size: 17px; line-height: 24px;
  }
  .contact__icon { width: 18px; height: 18px; flex: none; }

  /* back */
  .card--back { background: var(--navy); }
  .back-brand {
    position: absolute; right: 48px; bottom: 48px;
    display: flex; align-items: center; gap: 14px;
    color: var(--white);
  }
  .back-brand__mark { width: 40px; height: 40px; background: var(--white); }
  .back-brand__name { font-size: 26px; font-weight: 400; letter-spacing: 3px; }
</style>
</head>
<body>
<main class="sheet">
  <section class="card card--front" aria-label="Business card front">
    <div class="brand">
      <span class="brand__mark" aria-hidden="true"></span>
      <span class="brand__name">QUAYVALE</span>
      <span class="brand__tag">LEGAL</span>
    </div>

    <div class="holder">
      <p class="holder__name">Paul Whitcombe</p>
      <p class="holder__role">Managing Partner</p>
      <address class="holder__address">Level 9, 7 Ferris Lane<br>Sydney NSW 2000</address>
    </div>

    <div class="accent" aria-hidden="true"></div>

    <ul class="contact">
      <li class="contact__item">02 9364 2710
        <svg class="contact__icon" viewBox="0 0 18 18" aria-hidden="true"><circle cx="9" cy="9" r="9" fill="var(--icon-grey)"/><path d="M4 8c0-2 2-3 5-3s5 1 5 3h-3V7H7v1z M5 13l1.5-4h5L13 13z" fill="#000"/></svg>
      </li>
      <li class="contact__item">02 8472 3159
        <svg class="contact__icon" viewBox="0 0 18 18" aria-hidden="true"><circle cx="9" cy="9" r="9" fill="var(--icon-grey)"/><rect x="6" y="3" width="6" height="12" rx="1" fill="#000"/><rect x="7" y="4.5" width="4" height="7.5" fill="var(--icon-grey)"/></svg>
      </li>
      <li class="contact__item">paul@qvlegal.com.au
        <svg class="contact__icon" viewBox="0 0 18 18" aria-hidden="true"><circle cx="9" cy="9" r="9" fill="var(--icon-grey)"/><rect x="4" y="5.5" width="10" height="7" fill="#000"/><path d="M4 5.5l5 4 5-4" stroke="var(--icon-grey)" fill="none"/></svg>
      </li>
      <li class="contact__item">www.qvlegal.com.au
        <svg class="contact__icon" viewBox="0 0 18 18" aria-hidden="true"><circle cx="9" cy="9" r="9" fill="var(--icon-grey)"/><circle cx="9" cy="9" r="5" fill="none" stroke="#000" stroke-width="1.4"/><path d="M4 9h10M9 4c-2 3-2 7 0 10M9 4c2 3 2 7 0 10" stroke="#000" fill="none"/></svg>
      </li>
    </ul>
  </section>

  <section class="card card--back" aria-label="Business card back">
    <div class="back-brand">
      <span class="back-brand__mark" aria-hidden="true"></span>
      <span class="back-brand__name">QUAYVALE LEGAL</span>
    </div>
  </section>
</main>
</body>
</html>
```